Clear Plastic Card Design

I am looking to have a business card designed from my logo icon. I am looking to match the style of a different business card I have attached in the files.
Looking for a card that is plastic, with layers of transparency in the shape of my logo icon (also attached in the files) - not a circle like the other card. The winning design will incorporate the red icon logo on the front and back and include the charity's name, "Light for the Weary Souls" in the same or similar font, as well as an email and phone number. For now, use the email: email@lightfortheweary-mail.org and the phone number 555-382-7194.
We like how the sample business card has transparency, partial and full opacity layers and a matching color scheme. Files will need to be in vector so that our business card printing company can work with it.
UPDATE:
We've some excellent designs in, thank you everyone! I got an early review from the owner, and he requested a minor redirect to find his perfect design. He wants the design to stand out by NOT being a rectangle. Try instead a circle, square, or best yet - something that falls in the outline of the logo icon, either fully or partially. Thank you, everyone!
Light for the Weary Souls text should be incorporated as well as a phone and email.

```html
<!DOCTYPE html>
<html lang="en">
<head>
<meta charset="UTF-8">
<title>Light for the Weary Souls – Business Card</title>
<link rel="stylesheet" href="https://fonts.googleapis.com/css2?family=Poppins:wght@400&display=swap">
<style>
  :root {
    --backdrop: #e9e4dc;
    --card-fill: #f4f2ef;
    --card-edge: #b9b4ad;
    --ink: #1c1a1a;
    --brand-red: #b0201a;
    --rule: #5a5656;
  }
  * { margin: 0; padding: 0; box-sizing: border-box; }
  html, body {
    width: 1200px;
    height: 969px;
    overflow: hidden;
    background: var(--backdrop);
    font-family: "Poppins", sans-serif;
  }
  .card {
    position: absolute;
    left: 340px;
    top: 225px;
    width: 520px;
    height: 518px;
    background: var(--card-fill);
    border: 1.5px solid var(--card-edge);
    border-radius: 10px;
    color: var(--ink);
  }
  .brand-square {
    position: absolute;
    left: 300px;
    top: 70px;
    width: 140px;
    height: 140px;
    background: var(--brand-red);
  }
  .brand-name {
    position: absolute;
    left: 58px;
    top: 188px;
    font-size: 29px;
    line-height: 36px;
    font-weight: 400;
    color: var(--ink);
  }
  .contact-rule {
    position: absolute;
    top: 334px;
    left: 50px;
    width: 420px;
    height: 24px;
  }
  .contact-details {
    position: absolute;
    left: 0;
    right: 0;
    top: 383px;
    text-align: center;
    font-size: 21.5px;
    line-height: 28px;
    letter-spacing: 0.2px;
  }
</style>
</head>
<body>
  <div class="card">
    <div class="brand-square" aria-hidden="true"></div>
    <p class="brand-name">Light for the<br>Weary Souls</p>

    <svg class="contact-rule" viewBox="0 0 420 24" aria-hidden="true">
      <line x1="0" y1="12" x2="122" y2="12" stroke="var(--rule)" stroke-width="1"/>
      <line x1="270" y1="12" x2="420" y2="12" stroke="var(--rule)" stroke-width="1"/>
      <!-- phone -->
      <path d="M134 3 c2 -1 4 0 5 2 l2 4 c0 1 0 2 -1 3 l-1 1 c1 3 3 5 6 6 l1 -1 c1 -1 2 -1 3 -1 l4 2 c2 1 3 3 2 5 c-1 1 -3 2 -5 1 c-8 -3 -14 -9 -17 -17 c-1 -2 0 -4 1 -5 z" fill="var(--brand-red)"/>
      <!-- envelope -->
      <rect x="180" y="4" width="22" height="16" fill="var(--brand-red)"/>
      <path d="M180 5 l11 9 l11 -9" fill="none" stroke="var(--card-fill)" stroke-width="1.6"/>
      <!-- globe -->
      <circle cx="243" cy="12" r="11" fill="var(--brand-red)"/>
      <path d="M236 6 q4 3 3 7 q4 2 2 7 M248 4 q-3 4 1 6 q3 1 4 4" fill="none" stroke="var(--card-fill)" stroke-width="1.6"/>
    </svg>

    <div class="contact-details">
      <p class="contact-phone">555-382-7194</p>
      <p class="contact-email">email@lightfortheweary-mail.org</p>
      <p class="contact-web">www.lightfortheweary-souls.org</p>
    </div>
  </div>
</body>
</html>
```